Background on the company
=======================
This is a Bitcoin Consulting Company.

We have two projects.

Painted Tokens: software to trade assets over the Bitcoin protocol (assets like property, traditional currencies, gold, stocks, securities, bonds, etc.).

Vaultfern Home Steward: a hardware based web service in a box that manages cold storage wallets and off line transaction signing. It is the secure way to deploy a web wallet without relying on third parties.

All that to say this is a high tech company focusing on Bitcoin.

What does Wyndolmere mean?
========================

The Terror of Wyndolmere is the rabbit in Pelham Gristle's Silver Chalice that defeats his band of knights. (At least until they go and get the Sacred Brass Catapult).

We like this, because we are a deceptively soft and fuzzy company that is also killer!

What We Need:
============

Primarily we need to get the logo designed. I have a hand drawing I did, but you are not limited to that. And the logo needs to work on a business card. The right logo that works on a Business Card is the primary consideration.

The main task here is to get the logo right.  I have provided a drawing I made, and I like it, but my complaints are:  Wyndolmere is hard to read.  The 'C' isn't obvious.

We can fix this many ways.  We can forget the whole "combinde a rabit with the C and a" idea.  We can add "Wyndolmere Systems" on the card apart from the logo (that way if they don't "get it" they can still read it.)

The Rabbit itself is quite obviously scanned from a hand drawing.  That might not be a bad thing, but combine that with the entire logo, and it is too cheap looking.

Target Market(s)

Technical folks. Investors. Business contacts.

Industry/Entity Type

Software

Requirements
Must have
• We have to clean up the logo, or replace it with something that hints at the same sort of things. (See the upload) Basically and innocent white bunny. Something that works on a Business Card.

All the information below:

Derek Vale
ph (555) 314-9027
vale.derek@mailorbit.example
derek@wyndolmere.example
Nice to have
• I would like it to be serious, yet whimsical. An inside joke, so you get it if you know Pelham Gristle. But otherwise, it looks reasonably serious if you don't know Pelham Gristle.

I don't want it to be scary. (oddly, that my own efforts seem to make that easy to do)

Would like a set of colors that remind one of a cave, a rabbit, knights.... Not sure what those are...

```html
<!DOCTYPE html>
<html lang="en">
<head>
<meta charset="utf-8">
<title>Wyndolmere Systems — Business Card</title>
<link rel="stylesheet" href="https://fonts.googleapis.com/css2?family=Open+Sans:wght@400;700&display=swap">
<style>
  :root {
    --backdrop: #e6e4e1;
    --card: #ffffff;
    --ink-dark: #1c1c1c;
    --ink-mid: #8a8a8a;
    --ink-soft: #9a9a9a;
    --card-shadow: rgba(0, 0, 0, 0.18);
  }
  html, body {
    margin: 0;
    padding: 0;
    width: 1200px;
    height: 900px;
    overflow: hidden;
    background: var(--backdrop);
    font-family: "Open Sans", sans-serif;
  }
  .canvas {
    position: relative;
    width: 1200px;
    height: 900px;
    display: flex;
    align-items: center;
    justify-content: center;
  }
  .business-card {
    position: relative;
    width: 960px;
    height: 560px;
    background: var(--card);
    border-radius: 48px;
    box-shadow: 0 10px 30px var(--card-shadow);
  }
  .brand {
    position: absolute;
    left: 0;
    right: 0;
    top: 150px;
    height: 120px;
    display: flex;
    align-items: center;
    justify-content: center;
    gap: 24px;
  }
  .brand-mark {
    flex: none;
    width: 96px;
    height: 96px;
    background: var(--ink-dark);
  }
  .brand-name {
    font-size: 50px;
    font-weight: 700;
    color: var(--ink-dark);
    letter-spacing: -0.5px;
    line-height: 1;
    white-space: nowrap;
  }
  .contact-row {
    position: absolute;
    left: 0;
    right: 0;
    bottom: 64px;
    display: flex;
    align-items: center;
    justify-content: center;
    gap: 22px;
    font-size: 17px;
    color: var(--ink-soft);
    white-space: nowrap;
  }
  .contact-name {
    font-weight: 700;
    color: var(--ink-mid);
    font-size: 18px;
  }
  .contact-item {
    display: flex;
    align-items: center;
    gap: 6px;
  }
  .contact-icon {
    width: 16px;
    height: 16px;
    fill: var(--ink-mid);
  }
  .contact-icon--outline {
    fill: none;
    stroke: var(--ink-mid);
    stroke-width: 1.4;
  }
</style>
</head>
<body>
  <main class="canvas">
    <section class="business-card" aria-label="Wyndolmere Systems business card">
      <div class="brand">
        <span class="brand-mark"></span>
        <span class="brand-name">Wyndolmere Systems</span>
      </div>
      <div class="contact-row">
        <span class="contact-name">Derek Vale</span>
        <span class="contact-item">
          <svg class="contact-icon" viewBox="0 0 16 16" aria-hidden="true">
            <path d="M3.6 1.2l2.2 2.6c.3.4.3.9 0 1.3L4.7 6.3c.8 1.9 2.9 4 5 5l1.2-1.1c.4-.3.9-.3 1.3 0l2.6 2.2c.4.3.4.9.1 1.3l-1.2 1.3c-.5.5-1.2.7-1.9.5C6.6 14.3 1.7 9.4.5 4.2.3 3.5.5 2.8 1 2.3L2.3 1.1c.4-.3 1-.3 1.3.1z"/>
          </svg>
          (555) 314-9027
        </span>
        <span class="contact-item">
          <svg class="contact-icon contact-icon--outline" viewBox="0 0 16 16" aria-hidden="true">
            <path d="M1 3h14v10H1z M1 3l7 5.5L15 3"/>
          </svg>
          vale.derek@mailorbit.example
        </span>
        <span class="contact-item">derek@wyndolmere.example</span>
      </div>
    </section>
  </main>
</body>
</html>
```